PlumVesta screens tidy up

We would like advice on how to better present the following home page and overview pages.

The existing website is functional, but the pages don't appear professionals and pleasing to the eye. We would specifically like feedback on alignment and padding of icons and text to make the screen more appealing and polished.

We are following the quartzline design system.

1 page

Sans Serif
• IBM Plex, Poppins

```html
<!DOCTYPE html>
<html lang="en">
<head>
<meta charset="utf-8">
<title>PlumVesta screens</title>
<link href="https://fonts.googleapis.com/css2?family=Roboto:wght@400;500;700&display=swap" rel="stylesheet">
<style>
:root{
  --backdrop:#b1b1b1;
  --white:#ffffff;
  --ink:#2b2b2b;
  --ink-soft:#4a4a4a;
  --muted:#6b6b6b;
  --orange:#ee8626;
  --orange-soft:#fdf0e4;
  --side:#f7f8fc;
  --band:#ececec;
  --canvas:#f2f2f2;
  --bar:#3f3e3d;
  --line:#e3e3e3;
  --field:#f6f6f6;
}
*{box-sizing:border-box;margin:0;padding:0}
html,body{width:744px;height:1200px;overflow:hidden;background:var(--backdrop);font-family:"Roboto",sans-serif;color:var(--ink)}
.stage{position:absolute;left:0;top:0;width:1512px;height:2440px;transform:scale(0.49206);transform-origin:0 0}
.screen{position:absolute;left:109px;width:1295px;background:var(--canvas);overflow:hidden}
.abs{position:absolute}
.topbar{left:0;top:0;width:1295px;height:81px;background:var(--white)}
.brand{left:27px;top:14px;display:flex;align-items:center;gap:16px}
.brand-dot{width:50px;height:50px;border-radius:50%;background:var(--orange)}
.brand-name{font-size:32px;font-weight:500;color:var(--ink-soft);letter-spacing:-.3px}
.search{left:836px;top:14px;width:370px;height:54px;background:var(--field);border:1px solid var(--line);border-radius:3px}
.search span{position:absolute;left:24px;top:15px;font-size:17px;color:var(--ink-soft)}
.search-btn{position:absolute;right:4px;top:5px;width:52px;height:44px;background:#f6b13b;border-radius:2px;display:flex;align-items:center;justify-content:center}
.avatar{left:1229px;top:22px;width:38px;height:38px;border-radius:50%;background:var(--orange);display:flex;align-items:center;justify-content:center}
.sidebar{left:0;top:81px;width:237px;bottom:0;background:var(--side)}
.nav{position:absolute;left:0;width:237px;height:52px;display:flex;align-items:center;font-size:16px;color:var(--ink)}
.nav svg{position:absolute;left:28px}
.nav .label{position:absolute;left:62px}
.nav.active{background:var(--orange);color:var(--white);font-weight:500}
.nav.group{font-weight:500;padding-left:28px}
.nav.group.banded{background:var(--band)}
.nav.campaign{color:var(--orange);font-weight:500;padding-left:29px}
.nav.campaign svg{left:auto;right:16px}
.titlebar{left:237px;top:81px;right:0;height:52px;background:var(--bar);color:var(--white);display:flex;align-items:center;gap:20px}
.titlebar h1{font-size:21px;font-weight:500}
.titlebar small{font-size:14px}
.section-label{font-size:15px;font-weight:500;color:var(--ink)}
.card{background:var(--white)}
.card-title{font-size:20px;font-weight:500;color:var(--ink)}
.card-text{font-size:16px;color:var(--ink-soft)}
.icon-bubble{width:77px;height:77px;border-radius:50%;background:var(--orange-soft);display:flex;align-items:center;justify-content:center}
.art-bubble{width:104px;height:104px;border-radius:50%;background:radial-gradient(circle at 50% 55%,#f6cf56 0 30%,#eef0f2 31%)}
.stat{font-size:18px;font-weight:500;display:flex;align-items:center;gap:8px}
.progress{height:2px;background:#cfcfcf}
.progress i{display:block;width:8px;height:2px;background:var(--orange)}
.btn{background:var(--orange);color:var(--white);font-size:16px;font-weight:500;border-radius:2px;display:flex;align-items:center;justify-content:center}
.strong{color:var(--ink);font-weight:500}
</style>
</head>
<body>
<div class="stage">

<!-- Home screen -->
<section class="screen" style="top:107px;height:1029px">
  <header class="abs topbar">
    <div class="abs brand"><span class="brand-dot"></span><span class="brand-name">PlumVesta</span></div>
    <div class="abs search"><span>Search</span><div class="search-btn"><svg width="18" height="18" viewBox="0 0 18 18"><circle cx="7.5" cy="7.5" r="5" fill="none" stroke="#fff" stroke-width="2.4"/><path d="M11 11l5 5" stroke="#fff" stroke-width="2.4"/></svg></div></div>
    <div class="abs avatar"><svg width="16" height="18" viewBox="0 0 16 18"><circle cx="8" cy="5" r="4" fill="#fff"/><path d="M1 17c0-5 3-7 7-7s7 2 7 7z" fill="#fff"/></svg></div>
  </header>
  <nav class="abs sidebar">
    <div class="nav active" style="top:0"><svg width="16" height="14" viewBox="0 0 16 14"><path d="M8 1L1 7h2v6h4V9h2v4h4V7h2z" fill="#fff"/></svg><span class="label">Home</span></div>
    <div class="nav" style="top:60px"><svg width="18" height="18" viewBox="0 0 18 18"><path d="M9 1a5 5 0 015 5v5l2 3H2l2-3V6a5 5 0 015-5zM7 15h4a2 2 0 01-4 0z" fill="#333"/></svg><span class="label">All alerts</span></div>
    <div class="nav" style="top:108px"><svg width="20" height="16" viewBox="0 0 20 16"><circle cx="6" cy="4" r="3" fill="#333"/><circle cx="14" cy="4" r="3" fill="#333"/><path d="M0 14c0-4 3-6 6-6s6 2 6 6zM8 14c0-4 3-6 6-6s6 2 6 6z" fill="#333"/></svg><span class="label">Manage</span></div>
    <div class="nav group banded" style="top:168px">Compaigns</div>
    <div class="nav campaign" style="top:232px">My Custom Campaign<svg width="12" height="8" viewBox="0 0 12 8"><path d="M1 7l5-5 5 5" fill="none" stroke="#ee8626" stroke-width="1.6"/></svg></div>
    <div class="nav" style="top:272px"><svg width="16" height="16" viewBox="0 0 16 16"><circle cx="7" cy="7" r="5" fill="none" stroke="#333" stroke-width="2"/><path d="M10.5 10.5l4 4" stroke="#333" stroke-width="2"/></svg><span class="label">Overview</span></div>
    <div class="nav" style="top:318px"><svg width="14" height="17" viewBox="0 0 14 17"><path d="M1 1h8l4 4v11H1z" fill="none" stroke="#333" stroke-width="1.4"/><path d="M4 8h6M4 11h6M4 14h6" stroke="#333"/></svg><span class="label">Files&amp; HoneyTokens</span></div>
    <div class="nav" style="top:364px"><svg width="18" height="18" viewBox="0 0 18 18"><circle cx="6" cy="5" r="3" fill="none" stroke="#555" stroke-width="1.4"/><circle cx="12" cy="9" r="3" fill="none" stroke="#555" stroke-width="1.4"/><circle cx="6" cy="13" r="3" fill="none" stroke="#555" stroke-width="1.4"/></svg><span class="label">Resources</span></div>
    <div class="nav" style="top:410px"><svg width="16" height="17" viewBox="0 0 16 17"><path d="M8 1a4.5 4.5 0 014.5 4.5V10l2 3h-13l2-3V5.5A4.5 4.5 0 018 1zM6 14.5h4a2 2 0 01-4 0z" fill="none" stroke="#333" stroke-width="1.4"/></svg><span class="label">Alerts</span></div>
    <div class="nav" style="top:456px"><svg width="20" height="18" viewBox="0 0 20 18"><circle cx="7" cy="10" r="4.5" fill="none" stroke="#333" stroke-width="2.6" stroke-dasharray="2.4 1.2"/><circle cx="15" cy="5" r="3" fill="none" stroke="#333" stroke-width="2"/></svg><span class="label">Settings</span></div>
    <div class="nav campaign" style="top:503px">Default Campaign<svg width="12" height="8" viewBox="0 0 12 8"><path d="M1 1l5 5 5-5" fill="none" stroke="#ee8626" stroke-width="1.6"/></svg></div>
  </nav>
  <div class="abs titlebar" style="padding-left:34px"><h1>Home</h1></div>

  <div class="abs section-label" style="left:279px;top:182px">Teamspace</div>
  <div class="abs card" style="left:279px;top:224px;width:977px;height:103px">
    <div class="abs card-title" style="left:26px;top:24px">Default</div>
    <div class="abs card-text" style="left:26px;top:58px">The Default client is created as a part of your user account</div>
  </div>

  <div class="abs section-label" style="left:279px;top:345px">Subscription overview</div>
  <div class="abs section-label" style="left:777px;top:345px">Files&amp; HoneyTokens</div>
  <div class="abs card" style="left:279px;top:387px;width:482px;height:210px">
    <div class="abs icon-bubble" style="left:26px;top:28px"><svg width="46" height="44" viewBox="0 0 46 44"><g fill="none" stroke="#ee8626" stroke-width="2"><rect x="3" y="28" width="7" height="14"/><rect x="14" y="20" width="7" height="22"/><rect x="25" y="12" width="7" height="30"/><rect x="36" y="3" width="7" height="39"/></g></svg></div>
    <div class="abs card-title" style="left:26px;top:114px">Starter Pack Usage</div>
    <div class="abs card-text" style="left:26px;top:147px">0 Files active out of 10 allowed</div>
    <div class="abs progress" style="left:26px;top:181px;width:430px"><i></i></div>
  </div>
  <div class="abs card" style="left:777px;top:387px;width:482px;height:210px">
    <div class="abs icon-bubble" style="left:26px;top:28px"><svg width="40" height="46" viewBox="0 0 40 46"><g fill="none" stroke="#ee8626" stroke-width="2"><path d="M4 4h22v32H4z"/><path d="M10 10h24v26l-8 8H10z"/><path d="M15 18h14M15 23h14M15 28h14M15 33h8"/></g></svg></div>
    <div class="abs card-title" style="left:26px;top:114px">Statistics</div>
    <div class="abs stat" style="left:26px;top:153px">0 <svg width="24" height="24" viewBox="0 0 24 24"><circle cx="12" cy="12" r="10" fill="none" stroke="#333" stroke-width="1.8"/><path d="M7 12l4 4 8-9" fill="none" stroke="#333" stroke-width="1.8"/></svg></div>
    <div class="abs stat" style="left:206px;top:153px">30 <svg width="24" height="24" viewBox="0 0 24 24"><g fill="none" stroke="#333" stroke-width="1.4"><rect x="2" y="8" width="20" height="14"/><path d="M5 8V2h14v6M8 5h8M2 13h20"/></g></svg></div>
  </div>

  <div class="abs section-label" style="left:279px;top:617px">Campaigns</div>
  <div class="abs section-label" style="left:962px;top:617px">New Campaign</div>
  <div class="abs card" style="left:279px;top:656px;width:387px;height:332px">
    <div class="abs art-bubble" role="img" aria-label="Folder with documents and gear illustration" style="left:56px;top:34px"></div>
    <div class="abs card-title" style="left:56px;top:154px">My Custom Campaign</div>
    <div class="abs card-text" style="left:56px;top:190px">This is my custom camaign for finding</div>
    <div class="abs card-text" style="left:56px;top:231px"><span style="font-size:20px;margin-right:10px">0</span>Active <span class="strong">Files and HoneyTokens</span></div>
    <div class="abs card-text" style="left:56px;top:283px">Active since: Jul 25 2023 13:12</div>
  </div>
  <div class="abs card" style="left:686px;top:656px;width:387px;height:332px">
    <div class="abs art-bubble" role="img" aria-label="Folder with documents and gear illustration" style="left:33px;top:34px"></div>
    <div class="abs card-title" style="left:33px;top:154px">Default Campaign</div>
    <div class="abs card-text" style="left:33px;top:190px">Define your own mission or combine differen</div>
    <div class="abs card-text" style="left:33px;top:231px"><span style="font-size:20px;margin-right:10px">0</span>Active <span class="strong">Files and HoneyTokens</span></div>
    <div class="abs card-text" style="left:33px;top:283px">Active since: Jul 25 2023 12:17</div>
  </div>
</section>

<!-- Overview screen -->
<section class="screen" style="top:1234px;height:1100px">
  <header class="abs topbar">
    <div class="abs brand"><span class="brand-dot"></span><span class="brand-name">PlumVesta</span></div>
    <div class="abs search"><span>Search</span><div class="search-btn"><svg width="18" height="18" viewBox="0 0 18 18"><circle cx="7.5" cy="7.5" r="5" fill="none" stroke="#fff" stroke-width="2.4"/><path d="M11 11l5 5" stroke="#fff" stroke-width="2.4"/></svg></div></div>
    <div class="abs avatar"><svg width="16" height="18" viewBox="0 0 16 18"><circle cx="8" cy="5" r="4" fill="#fff"/><path d="M1 17c0-5 3-7 7-7s7 2 7 7z" fill="#fff"/></svg></div>
  </header>
  <nav class="abs sidebar">
    <div class="nav" style="top:3px"><svg width="16" height="14" viewBox="0 0 16 14"><path d="M8 1L1 7h2v6h4V9h2v4h4V7h2z" fill="#333"/></svg><span class="label">Home</span></div>
    <div class="nav" style="top:60px"><svg width="18" height="18" viewBox="0 0 18 18"><path d="M9 1a5 5 0 015 5v5l2 3H2l2-3V6a5 5 0 015-5zM7 15h4a2 2 0 01-4 0z" fill="#333"/></svg><span class="label">All alerts</span></div>
    <div class="nav" style="top:108px"><svg width="20" height="16" viewBox="0 0 20 16"><circle cx="6" cy="4" r="3" fill="#333"/><circle cx="14" cy="4" r="3" fill="#333"/><path d="M0 14c0-4 3-6 6-6s6 2 6 6zM8 14c0-4 3-6 6-6s6 2 6 6z" fill="#333"/></svg><span class="label">Manage</span></div>
    <div class="nav group" style="top:158px">Compaigns</div>
    <div class="nav campaign" style="top:201px">My Custom Campaign<svg width="12" height="8" viewBox="0 0 12 8"><path d="M1 7l5-5 5 5" fill="none" stroke="#ee8626" stroke-width="1.6"/></svg></div>
    <div class="nav active" style="top:262px"><svg width="16" height="16" viewBox="0 0 16 16"><circle cx="7" cy="7" r="5" fill="none" stroke="#fff" stroke-width="2"/><path d="M10.5 10.5l4 4" stroke="#fff" stroke-width="2"/></svg><span class="label">Overview</span></div>
    <div class="nav" style="top:314px"><svg width="14" height="17" viewBox="0 0 14 17"><path d="M1 1h8l4 4v11H1z" fill="none" stroke="#333" stroke-width="1.4"/><path d="M4 8h6M4 11h6M4 14h6" stroke="#333"/></svg><span class="label">Files&amp; HoneyTokens</span></div>
    <div class="nav" style="top:365px"><svg width="18" height="18" viewBox="0 0 18 18"><circle cx="6" cy="5" r="3" fill="none" stroke="#555" stroke-width="1.4"/><circle cx="12" cy="9" r="3" fill="none" stroke="#555" stroke-width="1.4"/><circle cx="6" cy="13" r="3" fill="none" stroke="#555" stroke-width="1.4"/></svg><span class="label">Resources</span></div>
    <div class="nav" style="top:417px"><svg width="18" height="16" viewBox="0 0 18 16"><path d="M9 1l8 14H1z" fill="#333"/><path d="M9 6v4M9 12v1.5" stroke="#fff" stroke-width="1.6"/></svg><span class="label">Alerts</span></div>
    <div class="nav" style="top:468px"><svg width="20" height="18" viewBox="0 0 20 18"><circle cx="7" cy="10" r="4.5" fill="none" stroke="#333" stroke-width="2.6" stroke-dasharray="2.4 1.2"/><circle cx="15" cy="5" r="3" fill="none" stroke="#333" stroke-width="2"/></svg><span class="label">Settings</span></div>
    <div class="nav campaign" style="top:503px">Default Campaign<svg width="12" height="8" viewBox="0 0 12 8"><path d="M1 1l5 5 5-5" fill="none" stroke="#ee8626" stroke-width="1.6"/></svg></div>
  </nav>
  <div class="abs titlebar" style="padding-left:46px"><h1>Overview</h1><small>My Cutom Campaign</small></div>

  <div class="abs section-label" style="left:279px;top:182px">Campaign</div>
  <div class="abs card" style="left:279px;top:224px;width:977px;height:103px">
    <div class="abs card-title" style="left:26px;top:24px">My Custom Campaign</div>
    <div class="abs card-text" style="left:26px;top:58px">This is my custom campaign for finding!</div>
    <div class="abs btn" style="left:825px;top:34px;width:114px;height:36px">Custom</div>
  </div>

  <div class="abs section-label" style="left:279px;top:345px">Campaign Organisation</div>
  <div class="abs card" style="left:279px;top:387px;width:988px;height:210px">
    <div class="abs icon-bubble" style="left:26px;top:28px"><svg width="46" height="40" viewBox="0 0 46 40"><g fill="none" stroke="#ee8626" stroke-width="2"><path d="M16 38V4h18v34M3 38V16h13M34 38h9V20h-9M1 38h44"/><path d="M21 10h3M27 10h3M21 16h3M27 16h3M21 22h3M27 22h3M7 22v10M11 22v10"/></g></svg></div>
    <div class="abs card-title" style="left:26px;top:114px">Self-enabling Deliverables Proprietary Limited</div>
    <div class="abs card-text" style="left:26px;top:164px">Standard</div>
    <div class="abs stat" style="left:364px;top:155px"><svg width="38" height="34" viewBox="0 0 38 34"><g fill="none" stroke="#333" stroke-width="1.4"><circle cx="19" cy="12" r="4"/><circle cx="7" cy="6" r="3"/><circle cx="31" cy="6" r="3"/><path d="M12 32V22a7 7 0 0114 0v10M2 24v-6a5 5 0 0110 0M36 24v-6a5 5 0 00-10 0"/></g></svg> <span style="margin-left:8px">86</span></div>
    <div class="abs card-title" style="left:518px;top:114px">Unleash Bleeding- edge Mindshare</div>
    <div class="abs card-text" style="left:518px;top:164px">8 hours ago</div>
    <div class="abs stat" style="left:856px;top:155px"><svg width="38" height="34" viewBox="0 0 38 34"><g fill="none" stroke="#333" stroke-width="1.4"><circle cx="19" cy="12" r="4"/><circle cx="7" cy="6" r="3"/><circle cx="31" cy="6" r="3"/><path d="M12 32V22a7 7 0 0114 0v10M2 24v-6a5 5 0 0110 0M36 24v-6a5 5 0 00-10 0"/></g></svg> <span style="margin-left:8px">8</span></div>
  </div>

  <div class="abs section-label" style="left:279px;top:626px">File &amp; HoneyTokens</div>
  <div class="abs section-label" style="left:786px;top:626px">Resources</div>
  <div class="abs card" style="left:279px;top:668px;width:482px;height:210px">
    <div class="abs icon-bubble" style="left:26px;top:28px"><svg width="40" height="46" viewBox="0 0 40 46"><g fill="none" stroke="#ee8626" stroke-width="2"><path d="M4 4h22v32H4z"/><path d="M10 10h24v26l-8 8H10z"/><path d="M15 18h14M15 23h14M15 28h14M15 33h8"/></g></svg></div>
    <div class="abs card-title" style="left:26px;top:116px">Statistices</div>
    <div class="abs stat" style="left:26px;top:155px">0 <svg width="24" height="24" viewBox="0 0 24 24"><circle cx="12" cy="12" r="10" fill="none" stroke="#333" stroke-width="1.8"/><path d="M7 12l4 4 8-9" fill="none" stroke="#333" stroke-width="1.8"/></svg></div>
    <div class="abs stat" style="left:206px;top:155px">30 <svg width="24" height="24" viewBox="0 0 24 24"><g fill="none" stroke="#333" stroke-width="1.4"><rect x="2" y="8" width="20" height="14"/><path d="M5 8V2h14v6M8 5h8M2 13h20"/></g></svg></div>
  </div>
  <div class="abs card" style="left:786px;top:668px;width:482px;height:210px">
    <div class="abs icon-bubble" style="left:26px;top:28px"><svg width="46" height="46" viewBox="0 0 46 46"><g fill="none" stroke="#ee8626" stroke-width="2"><path d="M17 4l6-3 6 3v7l-6 3-6-3z"/><path d="M7 20l8-4 8 4v10l-8 4-8-4zM23 20l8-4 8 4v10l-8 4-8-4zM15 24v10M31 24v10"/></g></svg></div>
    <div class="abs card-text" style="left:26px;top:118px;width:430px;line-height:27px">Generate a collection of fictional organisations,custom templates uploadded files and logos</div>
  </div>

  <div class="abs section-label" style="left:281px;top:898px">Alerts</div>
  <div class="abs card" style="left:281px;top:940px;width:986px;height:123px">
    <div class="abs icon-bubble" style="left:26px;top:23px"><svg width="46" height="40" viewBox="0 0 46 40"><path d="M23 2l21 36H2z" fill="none" stroke="#ee8626" stroke-width="2.4" stroke-linejoin="round"/><path d="M23 14v12M23 30v3" stroke="#ee8626" stroke-width="2.6"/></svg></div>
    <div class="abs card-text" style="left:130px;top:59px">Alerts statistices will appear here</div>
  </div>
</section>

</div>
</body>
</html>
```